Resposive web site in 4 languages + image gallery + logo design

We need a web page, which will work on all devices.
I have uploaded web page concept.
Company name: Praxelun
Industry/Entity Type
It Company
Logo Text
quality matters
Coding
Coded - Design and coding required
Number of Pages Required
1 page

```html
<!DOCTYPE html>
<html lang="en">
<head>
<meta charset="utf-8">
<title>Praxelun — Wood, Stone and Restoration</title>
<link rel="stylesheet" href="https://fonts.googleapis.com/css2?family=Open+Sans:wght@400;600;700&display=swap">
<style>
:root{
  --navy:#0b1526;
  --navy-deep:#050b16;
  --orange:#f39327;
  --link-blue:#2a8fe0;
  --ink:#333;
  --muted:#555;
  --line:#d3d3d3;
  --icon:#8a8a8a;
  --black:#0a0a0a;
  --about-bg:#1c1a17;
  --yellow:#f2d81b;
  --white:#fff;
}
*{box-sizing:border-box;margin:0;padding:0}
html,body{width:1200px;height:2571px;overflow:hidden;background:var(--white)}
body{font-family:"Open Sans",Arial,sans-serif;color:var(--ink)}
.page{position:relative;width:1200px;height:2571px;overflow:hidden}
.abs{position:absolute}

/* header */
.site-header{left:0;top:0;width:1200px;height:96px;background:radial-gradient(ellipse at 30% 0%,#17294a 0%,var(--navy) 45%,var(--navy-deep) 100%)}
.brand{left:154px;top:33px;font-size:22px;font-weight:700;color:var(--white);letter-spacing:.3px}
.lang{left:898px;top:13px;font-size:9px;font-weight:700;color:var(--white);letter-spacing:.4px;white-space:nowrap}
.lang span{color:#8a97ad;margin:0 3px}
.social-square{left:1034px;top:8px;width:21px;height:21px;background:#2b5aa7}
.main-nav{right:154px;top:52px;display:flex;gap:27px;font-size:11px;font-weight:700;color:var(--white);text-transform:uppercase}
.main-nav .active{color:var(--orange)}

/* hero */
.hero{left:0;top:96px;width:1200px;height:382px;background:#111}
.hero-panel{position:absolute;top:0;height:382px}
.hero-saw{left:0;width:132px;background:linear-gradient(160deg,#6b5a45,#3a3b3c 55%,#8a8070)}
.hero-stone{left:137px;width:134px;background:linear-gradient(180deg,#4a4a48,#6d6b66 50%,#3b3a38)}
.hero-brick{left:276px;width:924px;background:linear-gradient(100deg,#5c8cc9 0%,#8ab8ea 35%,#b9d6f3 55%,#c9764c 78%,#a84d2c 100%)}

.sub-nav{left:0;top:478px;width:1200px;height:47px;background:var(--black)}
.sub-nav a{position:absolute;top:13px;font-size:16px;color:var(--link-blue);text-decoration:none}
.quote-link{right:142px;top:15px;font-size:13px;font-weight:600;color:var(--orange);text-decoration:underline;white-space:nowrap}

/* services */
.section-title{left:0;width:1200px;text-align:center;font-size:19px;color:#222;letter-spacing:.3px}
.photo{box-shadow:0 6px 14px rgba(0,0,0,.25)}
.service-title{font-size:25px;font-weight:700;color:var(--orange);letter-spacing:.3px}
.service-text{font-size:11.2px;line-height:19px;color:#444}
.btn-grid{display:grid;grid-template-columns:236px 236px;column-gap:13px;row-gap:11px}
.service-btn{height:38px;border:1px solid var(--line);display:flex;align-items:center;justify-content:space-between;padding:0 13px 0 14px;font-size:13.5px;color:#444;letter-spacing:.5px;text-transform:uppercase;background:var(--white);white-space:nowrap}
.service-btn svg{width:22px;height:22px;stroke:var(--icon);fill:none;stroke-width:1.6}

/* about */
.about{left:0;top:1673px;width:1200px;height:374px;background:radial-gradient(ellipse at 80% 30%,#2a2620,var(--about-bg) 60%,#0f0e0c)}
.about-photo{left:0;top:0;width:578px;height:374px;clip-path:polygon(0 0,578px 0,540px 374px,0 374px);background:linear-gradient(120deg,#3b342c 0%,#6a5640 40%,#8d6d4a 65%,#4a3d30 100%)}
.about-title{left:620px;top:30px;font-size:26px;font-weight:700;color:var(--white)}
.about-text{left:620px;width:420px;font-size:11.2px;line-height:20px;color:#e8e8e8}
.about-lead{left:620px;top:152px;width:400px;font-size:13.5px;line-height:23px;font-weight:700;color:var(--white)}
.about-lead em{font-style:normal;color:var(--orange)}
.about-rule{left:620px;width:406px;height:1px;background:#55504a}
.about-brand{left:620px;top:320px;font-size:20px;font-weight:700;color:var(--white)}
.badge{left:862px;top:312px;width:164px;height:58px;background:var(--yellow);border:3px solid #111;transform:rotate(-5deg)}

/* contact */
.contact-title{left:0;top:2085px;width:1200px;text-align:center;font-size:26px;font-weight:700;color:var(--orange)}
.contact-sub{left:0;top:2140px;width:1200px;text-align:center;font-size:13px;color:#222}
.mascot{left:178px;top:2206px;width:172px;height:180px;border-radius:50%;background:radial-gradient(circle at 50% 45%,#7fb35a 0%,#3f7b3a 55%,#2c2c2c 70%,#fff 71%)}
.address-head{left:403px;top:2206px;font-size:12px;font-weight:700;color:#111}
.contact-line{left:403px;font-size:12px;color:#333;display:flex;gap:12px;align-items:flex-start;line-height:21px;white-space:nowrap}
.contact-line svg{width:12px;height:12px;margin-top:4px;fill:#444;flex:none}
.field{left:701px;width:290px;height:28px;border:1px solid #ddd;font-size:10px;color:#777;padding:8px 10px}
.send{left:701px;top:2381px;width:86px;height:31px;background:var(--orange);color:var(--white);font-size:12px;font-weight:700;display:flex;align-items:center;justify-content:center}

/* footer */
.site-footer{left:0;top:2460px;width:1200px;height:111px;background:var(--black)}
.footer-nav{left:0;top:19px;width:1200px;display:flex;justify-content:center;gap:26px;font-size:13px;color:var(--white)}
.footer-social{left:0;top:56px;width:1200px;display:flex;justify-content:center;gap:4px}
.footer-social span{width:23px;height:23px;background:#5b6b85}
.copyright{left:0;top:88px;width:1200px;text-align:center;font-size:9px;color:#ddd}
</style>
</head>
<body>
<div class="page">

  <header class="site-header abs">
    <div class="brand abs">Praxelun</div>
    <div class="lang abs">EST<span>::</span>RUS<span>::</span>FIN<span>::</span>ENG</div>
    <div class="social-square abs" aria-label="Social page"></div>
    <nav class="main-nav abs"><span class="active">Services</span><span>About us</span><span>Contact</span></nav>
  </header>

  <section class="hero abs">
    <div class="hero-panel hero-saw" role="img" aria-label="Carpenter cutting a wooden board with a hand saw"></div>
    <div class="hero-panel hero-stone" role="img" aria-label="Mallet setting paving stones"></div>
    <div class="hero-panel hero-brick" role="img" aria-label="Builder in a hard hat laying a brick wall under a blue sky"></div>
  </section>

  <nav class="sub-nav abs">
    <a style="left:15px">Wood Works</a>
    <a style="left:151px">Stone Works</a>
    <a style="left:279px">Restoration</a>
    <span class="quote-link abs">Are you interested in an estimate? GET A QUOTE</span>
  </nav>

  <h2 class="section-title abs" style="top:546px;font-weight:400">OUR SERVICES</h2>

  <!-- Wood works -->
  <div class="photo abs" style="left:161px;top:631px;width:357px;height:288px;background:linear-gradient(135deg,#2a1c12,#8a5a2c 45%,#c98a3e 60%,#3a2a1a)" role="img" aria-label="Woodturner shaping a piece on a lathe with sparks"></div>
  <h3 class="service-title abs" style="left:552px;top:626px">WOOD WORKS</h3>
  <p class="service-text abs" style="left:552px;top:666px;width:486px">Timber is, in essence, a natural and warm material. Wood is also relatively durable and easy to work with, which has made it a favourite of builders throughout history. Our goal is to offer suitable products and quality furniture with installation and after-sales service to all of our clients.In order toachieve this, we're ready to help our clients in all stages of construction from design to production and maintenance.</p>
  <div class="btn-grid abs" style="left:552px;top:774px">
    <div class="service-btn">Furniture<svg viewBox="0 0 24 24"><path d="M4 12h16v5H4zM6 12V8h12v4M5 17v2M19 17v2"/></svg></div>
    <div class="service-btn">Windows<svg viewBox="0 0 24 24"><rect x="4" y="6" width="16" height="13"/><path d="M12 6v13M4 12h16M9 4h6"/></svg></div>
    <div class="service-btn">Doors<svg viewBox="0 0 24 24"><rect x="7" y="3" width="10" height="18"/><circle cx="14.5" cy="12" r=".8"/></svg></div>
    <div class="service-btn">Staircases<svg viewBox="0 0 24 24"><path d="M4 20h4v-4h4v-4h4V8h4V4M4 4v16"/></svg></div>
    <div class="service-btn">Woodcarving<svg viewBox="0 0 24 24"><path d="M3 19h18M6 16l10-10 2 2L8 18zM14 8l2 2"/></svg></div>
    <div class="service-btn">Graining<svg viewBox="0 0 24 24"><path d="M3 12l9-7 9 7M5 11v9h14v-9M10 20v-5h4v5"/></svg></div>
  </div>

  <!-- Stone works -->
  <h3 class="service-title abs" style="left:161px;top:970px">STONE WORKS</h3>
  <p class="service-text abs" style="left:161px;top:1009px;width:490px">The natural stone found in the ground has been used in construction for centuries because of its durability. A structure built by a skilled craftsman from natural stone is unique, genuine and durable, and perfect for our bracing climate. Our experienced craftsmen are ready to help you in all stages of construction from planning to completion.</p>
  <div class="btn-grid abs" style="left:161px;top:1119px;grid-template-columns:235px 235px;column-gap:12px">
    <div class="service-btn">Walls<svg viewBox="0 0 24 24"><path d="M3 6h18v12H3zM3 10h18M3 14h18M9 6v4M15 6v4M6 10v4M12 10v4M18 10v4M9 14v4M15 14v4"/></svg></div>
    <div class="service-btn">Terraces<svg viewBox="0 0 24 24"><path d="M4 11h16M6 11v9M18 11v9M10 11v9M14 11v9M8 11l4-6 4 6M4 20h16"/></svg></div>
    <div class="service-btn">Paths<svg viewBox="0 0 24 24"><path d="M3 14l4-3 4 3-4 3zM11 10l4-3 4 3-4 3zM13 17l4-3 4 3-4 3z"/></svg></div>
    <div class="service-btn">Outdoor kitchens<svg viewBox="0 0 24 24"><path d="M5 9h14a7 5 0 0 1-14 0zM12 3v3M9 4v2M15 4v2M8 14l-2 7M16 14l2 7"/></svg></div>
    <div class="service-btn">Fireplaces<svg viewBox="0 0 24 24"><path d="M12 3c3 4 6 7 6 11a6 6 0 0 1-12 0c0-3 2-5 3-6 0 2 1 3 2 3 0-3 0-5 1-8z"/></svg></div>
    <div class="service-btn">Smokeries<svg viewBox="0 0 24 24"><path d="M6 10a4 4 0 0 1 6-4 4 4 0 0 1 7 3 4 4 0 0 1-2 8H8a4 4 0 0 1-2-7z"/></svg></div>
    <div class="service-btn">Fences<svg viewBox="0 0 24 24"><path d="M4 20V7l1-2 1 2v13M10 20V7l1-2 1 2v13M16 20V7l1-2 1 2v13M3 10h18M3 16h18"/></svg></div>
  </div>
  <div class="photo abs" style="left:680px;top:982px;width:357px;height:288px;background:linear-gradient(160deg,#5a5a5c,#7b7d80 40%,#a2585a 60%,#4a4b4d)" role="img" aria-label="Gloved hands laying paving blocks"></div>

  <!-- Restoration -->
  <div class="photo abs" style="left:161px;top:1342px;width:357px;height:288px;background:linear-gradient(135deg,#9aa6b0,#d8dde2 40%,#b7c3cc 60%,#5e7a94)" role="img" aria-label="Two craftsmen shaking hands in a workshop"></div>
  <h3 class="service-title abs" style="left:552px;top:1338px">RESTORATION</h3>
  <p class="service-text abs" style="left:552px;top:1374px;width:490px">It's good to see that fixing old things has become popular again in recent years and people are trying to find ways to preserve valuable old windows and pieces of furniture before deciding to It is possible to give a new life to almost any wooden door, window, piece of furniture or staircase. The extensive experience of our craftsmen will help you achieve the desired result.</p>
  <div class="btn-grid abs" style="left:552px;top:1486px">
    <div class="service-btn">Furniture<svg viewBox="0 0 24 24"><path d="M4 12h16v5H4zM6 12V8h12v4M5 17v2M19 17v2"/></svg></div>
    <div class="service-btn">Windows<svg viewBox="0 0 24 24"><rect x="4" y="6" width="16" height="13"/><path d="M12 6v13M4 12h16M9 4h6"/></svg></div>
    <div class="service-btn">Doors<svg viewBox="0 0 24 24"><rect x="7" y="3" width="10" height="18"/><circle cx="14.5" cy="12" r=".8"/></svg></div>
    <div class="service-btn">Staircases<svg viewBox="0 0 24 24"><path d="M4 20h4v-4h4v-4h4V8h4V4M4 4v16"/></svg></div>
    <div class="service-btn">Floors<svg viewBox="0 0 24 24"><path d="M2 12l10-5 10 5-10 5zM7 9.5l10 5M12 7l-5 7.5M17 9.5l-10 5"/></svg></div>
    <div class="service-btn">Special projects<svg viewBox="0 0 24 24"><circle cx="9" cy="10" r="4"/><circle cx="17" cy="16" r="3"/><circle cx="9" cy="10" r="1.3"/></svg></div>
  </div>

  <!-- About -->
  <section class="about abs">
    <div class="about-photo abs" role="img" aria-label="Craftsman restoring an upholstered chair in his workshop"></div>
    <h2 class="about-title abs">ABOUT US</h2>
    <p class="about-text abs" style="top:76px">Praxelun is a company whose business operations include making wooden products, restoration and building structures from natural stone.</p>
    <div class="about-rule abs" style="top:132px"></div>
    <p class="about-lead abs">All of our products are made by <em>craftsmen and specialists</em> who have extensive experience and knowledge in their fields.</p>
    <div class="about-rule abs" style="top:221px"></div>
    <p class="about-text abs" style="top:240px">The products we offer are always handmade and we take the requests and ideas of the specific client into account We always strive to achieve the best possible quality.</p>
    <div class="about-brand abs">Praxelun</div>
    <div class="badge abs" role="img" aria-label="Quality badge"></div>
  </section>

  <!-- Contact -->
  <h2 class="contact-title abs">CONTACT US</h2>
  <p class="contact-sub abs">CONTACTPLEASE FILL IN THE FOLLOWING FIELDS IF YOU WOULD LIKE A PRICE QUOTE</p>
  <div class="mascot abs" role="img" aria-label="Cartoon carpenter in a cap carrying a plank"></div>
  <div class="address-head abs">Address</div>
  <div class="contact-line abs" style="top:2233px"><svg viewBox="0 0 12 12"><path d="M6 0a4 4 0 0 0-4 4c0 3 4 8 4 8s4-5 4-8a4 4 0 0 0-4-4zm0 5.5a1.5 1.5 0 1 1 0-3 1.5 1.5 0 0 1 0 3z"/></svg><span>Kaske 12<br>10115 Tallinn</span></div>
  <div class="contact-line abs" style="top:2305px"><svg viewBox="0 0 12 12"><path d="M2.5 0l2 3-1.3 1.3a7 7 0 0 0 4.5 4.5L9 7.5l3 2-1.5 2.5C5 12 0 7 0 1.5z"/></svg><span>Telephone: +372 55 12 345</span></div>
  <div class="contact-line abs" style="top:2328px"><svg viewBox="0 0 12 12"><path d="M0 2h12v8H0zM0 2l6 4 6-4" stroke="#fff" stroke-width=".8"/></svg><span>e-mail: info@praxelun.ee</span></div>

  <div class="field abs" style="top:2190px">Name</div>
  <div class="field abs" style="top:2231px">Telephone</div>
  <div class="field abs" style="top:2272px">Estonia E-mail</div>
  <div class="field abs" style="top:2312px;height:60px">Message</div>
  <div class="send abs">SEND</div>

  <!-- Footer -->
  <footer class="site-footer abs">
    <nav class="footer-nav abs"><span>Home</span><span>Services</span><span>About Us</span><span>Contact Us</span></nav>
    <div class="footer-social abs"><span></span><span></span><span></span><span></span><span></span></div>
    <p class="copyright abs">2016 © www.praxelun.ee</p>
  </footer>

</div>
</body>
</html>
```